Website redesign for Halt and Fullmane

We would like to update the design of our current website to a more concise, conversion optimized design.
The goal of our website is to get our message across as concisely as possible plus encourage people to contact us for more information or to book a consultation.
We need a redesign of the home page and 1 internal page - just for design/layout purposes/format purposes.

Target Market(s)

Males 20-45 years old who are concerned about hair loss and who want to regrow their own hair.

Industry/Entity Type

Health And Wellness

Number of Pages Required

2 page

Font styles to use
Sans Serif

Colors
00a990
33a6d7
ffffff
9d9d9d

Requirements
Must have
• We want the home page to be very concise and to the point in getting the message across. We want to get across the following 6 key messages:
• 1. Dr Pembrook story – why he created this solution
• 2. Hair loss is caused by a chemical imbalance
• 3. Halt and fullmane conducts genetic and DNA analysis, then rebalances body chemistry, thus reversing the hair loss process and enabling your own hair to regrow naturally
• 4. Money back guaranteed results
• 5. Purely Core ingredients – no harsh preservatives or chemicals are included
• 6. All ingredients are FDA approved and safe – no side effects
• We also need a strong call to action. We want people to call or email us to find out more information or to schedule a consultation.
• Here is our current website which is not performing as we would hope: http://www.haltandfullmane.example/
• Here is our press release for further information: https://www.pressdeskhub.example/news/finally-we-now-have-a-cure-for-male-pattern-baldness-28461902
• I uploaded the logo files, but let me know if anything else is needed and I can add it.

```html
<!DOCTYPE html>
<html lang="en">
<head>
<meta charset="utf-8">
<title>Halt and Fullmane — Home</title>
<link href="https://fonts.googleapis.com/css2?family=Raleway:wght@400;500;600;700;800&display=swap" rel="stylesheet">
<style>
:root{
  --teal:#00a990;
  --teal-dark:#009b83;
  --blue:#33a6d7;
  --white:#ffffff;
  --grey:#9d9d9d;
  --panel:#f2f2f2;
  --band:#ececec;
  --card-line:#d9e9e5;
}
*{box-sizing:border-box;margin:0;padding:0}
html,body{width:1200px;height:2601px;overflow:hidden;background:var(--white)}
body{font-family:'Raleway',Arial,sans-serif;color:var(--grey)}
.page{position:relative;width:1200px;height:2601px;overflow:hidden}
a{color:var(--teal);text-decoration:none}

/* header */
.site-header{position:absolute;left:0;top:0;width:1200px;height:137px;background:var(--teal)}
.brand{position:absolute;left:110px;top:50px;display:flex;align-items:center;gap:14px;color:var(--white);font-weight:500;font-size:32px;letter-spacing:.3px}
.brand-dot{width:26px;height:26px;border-radius:50%;background:var(--white)}
.phone-tab{position:absolute;left:891px;top:0;width:200px;height:49px;background:var(--white);border-radius:0 0 22px 22px;color:var(--teal);font-size:15px;font-weight:500;display:flex;align-items:center;justify-content:center}
.main-nav{position:absolute;top:66px;left:0;height:71px}
.main-nav a{position:absolute;top:0;height:71px;line-height:50px;color:var(--white);font-size:15px;font-weight:500;white-space:nowrap}
.main-nav a.active{background:var(--white);color:var(--teal);text-align:center;width:78px}

/* hero */
.hero{position:absolute;left:0;top:137px;width:1200px;height:536px;background:linear-gradient(100deg,#5d4c42 0%,#8a7363 30%,#b79a86 52%,#9e8473 70%,#6f5b4f 100%)}
.hero-shade{position:absolute;inset:0;background:rgba(40,30,25,.28)}
.hero-title{position:absolute;left:0;top:250px;width:1200px;text-align:center;color:var(--white)}
.hero-title h1{font-size:51px;font-weight:800;letter-spacing:2px;line-height:1}
.hero-title p{font-size:37px;font-weight:400;margin-top:10px;line-height:1}
.btn-consult{position:absolute;left:465px;top:466px;width:272px;height:58px;border:3px solid var(--white);border-radius:4px;color:var(--white);font-size:13px;font-weight:700;letter-spacing:1px;display:flex;align-items:center;justify-content:center}

.live-tab{position:absolute;left:0;top:477px;width:47px;height:312px;background:var(--white);border:3px solid var(--blue);border-left:none;border-radius:0 6px 6px 0;z-index:3}
.live-tab span{position:absolute;left:10px;top:260px;transform:rotate(-90deg);transform-origin:left top;white-space:nowrap;color:var(--blue);font-size:13px;letter-spacing:1.5px;font-weight:500}
.live-tab i{position:absolute;left:6px;bottom:6px;width:30px;height:30px;border-radius:6px;background:var(--blue)}

/* messages */
.message-band{position:absolute;left:0;top:673px;width:1200px;height:588px;background:var(--band)}
.teal-band{position:absolute;left:0;top:1261px;width:1200px;height:653px;background:var(--teal)}
.card{position:absolute;width:309px;background:var(--panel);border:2px solid var(--card-line);border-radius:3px;text-align:center;overflow:hidden}
.card h2{height:70px;background:var(--teal);color:var(--white);font-size:24px;font-weight:400;display:flex;align-items:center;justify-content:center;gap:14px;letter-spacing:.3px;white-space:nowrap}
.card h2::before,.card h2::after{content:"";width:26px;height:2px;background:var(--white);flex:none}
.card h2.tight::before,.card h2.tight::after{width:10px}
.card-body{padding:24px 24px 0;font-size:13.5px;font-weight:600;line-height:22px;color:var(--grey)}
.card-body a{font-weight:700}
.card-link{position:absolute;left:0;right:0;bottom:22px;font-size:13.5px;font-weight:700;color:var(--teal);white-space:nowrap}

/* testimonial */
.testimonial-head{position:absolute;left:0;top:1368px;width:1200px;text-align:center;color:var(--white);font-size:30px;font-weight:700;line-height:40px}
.video{position:absolute;left:387px;top:1479px;width:426px;height:267px;background:#000}
.video-frame{position:absolute;left:0;top:14px;width:426px;height:240px;background:linear-gradient(90deg,#4a5560 0%,#7b8a92 40%,#b9c3c7 70%,#dfe6e8 100%)}
.video-play{position:absolute;left:190px;top:120px}
.caption{position:absolute;left:380px;top:1775px;width:440px;text-align:center;color:var(--white);font-size:13.5px;font-weight:600;line-height:17.5px}
.caption b{font-weight:800}

/* faqs */
.faqs{position:absolute;left:0;top:1914px;width:1200px;height:415px;background:var(--panel)}
.faqs h2{position:absolute;left:0;top:57px;width:1200px;text-align:center;color:var(--teal);font-size:31px;font-weight:400}
.faq{position:absolute;top:128px;width:390px;color:var(--teal)}
.faq h3{font-size:24px;font-weight:600;margin-bottom:16px}
.faq p{font-size:13.5px;line-height:24px;font-weight:500}
.faq-more{position:absolute;left:659px;top:2267px;font-size:14px;font-weight:700;color:var(--teal)}

/* footer */
.site-footer{position:absolute;left:0;top:2329px;width:1200px;height:272px;background:var(--teal);color:var(--white)}
.footer-col{position:absolute;top:55px;font-size:13.5px;line-height:17px}
.footer-col h4{font-size:14px;font-weight:700;margin-bottom:16px}
.contact-form .field{position:absolute;background:var(--white);border-radius:8px;color:var(--grey);font-size:13px;padding:7px 14px}
.send{position:absolute;left:635px;top:197px;width:128px;height:28px;border:2px solid var(--white);border-radius:14px;color:var(--white);font-size:11px;display:flex;align-items:center;justify-content:center}
.social{position:absolute;top:199px;width:28px;height:28px;border-radius:5px;background:var(--white)}
</style>
</head>
<body>
<div class="page">

  <header class="site-header">
    <div class="brand"><span class="brand-dot"></span>Halt &amp; Fullmane</div>
    <div class="phone-tab">CALL US: (555) 014-2290</div>
    <nav class="main-nav">
      <a style="left:503px">ABOUT US</a>
      <a style="left:620px">HOW IT WORKS</a>
      <a class="active" style="left:753px">BLOG</a>
      <a style="left:858px">SALON PARTNERS</a>
      <a style="left:1026px">CONTACT</a>
    </nav>
  </header>

  <section class="hero" role="img" aria-label="Photo of a young man checking his hairline in a mirror">
    <div class="hero-shade"></div>
  </section>
  <div class="hero-title">
    <h1>THE REVOLUTIONARY NEW SOLUTION</h1>
    <p>FOR HAIR LOSS THAT USES PERSONALIZED MEDICINE</p>
  </div>
  <a class="btn-consult">SCHEDULE A CONSULTATION</a>

  <div class="live-tab"><span>LIVE REPRESENTATIVE AVAILABLE</span><i></i></div>

  <div class="message-band"></div>
  <div class="teal-band"></div>

  <article class="card" style="left:111px;top:629px;height:321px">
    <h2>THE STORY</h2>
    <p class="card-body">Dr. Julian Pembrook, the creator of Halt and Fullmane is a renowned hair restoration expert. After seeing first his father and then older brothers thin and go bald, he dedicated his life to finding the cure for hair loss.</p>
    <a class="card-link">Read more of Dr Pembrook story here.</a>
  </article>
  <article class="card" style="left:446px;top:629px;height:321px">
    <h2>THE CAUSE</h2>
    <p class="card-body">The vast majority of cases we see do have at least some component of hereditary baldness as part of the mix. The reason it is hereditary is due to a small defect on one (hereditary) gene which causes our bodies to over-produce the hormone DHT.</p>
    <a class="card-link">How stopping hair loss can save your life.</a>
  </article>
  <article class="card" style="left:780px;top:629px;height:321px">
    <h2>THE SOLUTION</h2>
    <p class="card-body">Halt and fullmane conducts genetic and DNA analysis, then rebalances body chemistry, thus reversing the hair loss process and enabling your own hair to regrow naturally.</p>
    <a class="card-link">How stopping hair loss can save your life.</a>
  </article>

  <article class="card" style="left:111px;top:988px;height:323px">
    <h2>THE GARANTEE</h2>
    <p class="card-body">Dr. Pembrook is so confident of the effectiveness of this solution he is providing <a>his personal guarantee</a>.</p>
  </article>
  <article class="card" style="left:446px;top:988px;height:323px">
    <h2 class="tight">THE&nbsp; INGREDIENTS</h2>
    <p class="card-body">Purely Core ingredients – no harsh preservatives or chemicals are included. Dr. Pembrook created his solution from a combination of FDA-approved active ingredients. The combination of medicines we use are clinically proven to both block DHT and stimulate hair growth.<br><a>You can find more details on this here.</a></p>
  </article>
  <article class="card" style="left:780px;top:988px;height:323px">
    <h2 class="tight">NO SIDE EFFECTS</h2>
    <p class="card-body">All ingredients are FDA approved and safe. We have had zero side effects reported to either us or the pharmacy. Dr Pembrook personalizes your dose based on your DNA and THAT makes all the difference. You can read more about it <a>here</a>.</p>
  </article>

  <h2 class="testimonial-head">Our clients love keeping and growing their hair back.<br>You can too!</h2>
  <div class="video">
    <div class="video-frame" role="img" aria-label="Video still of a client talking about his results"></div>
    <svg class="video-play" width="46" height="30" viewBox="0 0 46 30" aria-hidden="true">
      <rect width="46" height="30" rx="5" fill="#1c1c1c" fill-opacity=".85"/>
      <path d="M18 8 L30 15 L18 22 Z" fill="#ffffff"/>
    </svg>
  </div>
  <p class="caption">Marcus first came to see me four months ago. Here he tells the story about how he first realized he was receding and losing his hair as well as his experience with the Halt and Fullmane personalized program so far.<br>Read more <b>Success Stories</b></p>

  <section class="faqs">
    <h2>QUICK FAQS</h2>
    <div class="faq" style="left:165px">
      <h3>How Much Does It Cost?</h3>
      <p>For just a small monthly charge, we will provide you with your personalized solution. The cost will vary depending on the stage of your hair thinning or loss and your genetic make-up. Typical monthly costs range between $99 up to $199 per month depending on how severe your case is plus there is a discount for paying annually in advance. There is also a fee for your lab tests if you do not have insurance to cover this. Tax deductions may also apply for some patients.</p>
    </div>
    <div class="faq" style="left:659px;width:395px">
      <h3>How long does it take?</h3>
      <p>After three to six months you will start to see hair loss stop. After 6 to 9 months you will start to see your hair regrow. It is important to act before any of your hair follicles die. Once they have died they cannot be regrown.</p>
    </div>
  </section>
  <a class="faq-more">Read more Frequently Asked Questions.</a>

  <footer class="site-footer">
    <div class="footer-col" style="left:134px">
      <h4>Address</h4>
      <p>Halt and Fullmane Hair, LLC<br>2180 Harbor Crest Ave, Suite 410<br>Lakeview CA 90077</p>
    </div>
    <div class="footer-col" style="left:350px">
      <h4>Hours of Operation</h4>
      <p>Monday - Friday: 9.00am to 5.00pm<br>Saturday: 8.00am to 2.00pm<br>Call Us (555) 014-2290<br>&nbsp;(555) 014-2290</p>
    </div>
    <div class="footer-col contact-form" style="left:636px;width:420px">
      <h4>Have more question? Email us!</h4>
    </div>
    <div class="contact-form">
      <div class="field" style="left:636px;top:76px;width:200px;height:30px">Your Name...</div>
      <div class="field" style="left:857px;top:76px;width:199px;height:30px">Your e-mail...</div>
      <div class="field" style="left:636px;top:116px;width:420px;height:70px">Message...</div>
    </div>
    <div class="send">Send message</div>
    <span class="social" style="left:134px"></span>
    <span class="social" style="left:186px"></span>
    <span class="social" style="left:239px"></span>
    <span class="social" style="left:291px"></span>
  </footer>

</div>
</body>
</html>
```